"Where Rivers Bend" Book Cover Design

I need a design for the cover of a book I have written. I'm attaching the lead into the book to help provide context for you. I want the cover to be unique and outside of the box while still staying in line with the energy and feel of the content.

"Wine always had a way of speaking to me, even if I didn’t quite understand what it was saying. Upon making a decision to spend my life pursuing wine, I began to hear it loud and clear. I knew it had to be more than rich man’s drink, lifestyle trend, or just frivolous alcohol. I resolved it had a deeper meaning. In the years of trying to understand wine’s whole story, it ended up crafting mine.
Where Rivers Bend is the intertwining of two personal stories, one about wine and one about myself. My goal is to tell wine’s story in tandem with my own. In this way, I can give wine the authentic voice it deserves. I want you to learn about wine like I learned, little by little. Each Wine 101 chapter seeks to answer the most common questions and misconceptions I have encountered with wine throughout the years. Every wine chapter will give you a foundation to build on, more confidence, and a greater love for wine."

Thank you for your time!

Target Market(s)

Men and Women Wine Lovers between the ages of 25-50

Colors

Designer to choose colors to be used in the design.

Requirements
Must have
• An eye catching appeal. Connect the title with the contents and convey the spirit of the book. A way to showcase the contents without being overly obvious and still having some mystery to the contents. Invite the potential reader to look deeper.

```html
<!DOCTYPE html>
<html lang="en">
<head>
<meta charset="utf-8">
<title>Where Rivers Bend — Book Cover</title>
<link href="https://fonts.googleapis.com/css2?family=Great+Vibes&display=swap" rel="stylesheet">
<style>
  :root {
    --page-bg: #e9e6e1;
    --sky-top: #17224f;
    --sky-mid: #26346f;
    --cloud-band: #4f5e96;
    --horizon-gold: #e6b152;
    --horizon-ember: #c7682a;
    --sea-dusk: #2c2c3c;
    --foreground-dark: #0d0f16;
    --wine-gold: #e9c15e;
    --wine-amber: #b98a3a;
    --glass-edge: #8a96b8;
    --title-ink: #f7f4ee;
    --author-ink: #dff3ec;
  }
  html, body {
    margin: 0;
    padding: 0;
    width: 1200px;
    height: 960px;
    overflow: hidden;
    background: var(--page-bg);
  }
  .canvas {
    position: relative;
    width: 1200px;
    height: 960px;
  }
  .book-cover {
    position: absolute;
    left: 320px;
    top: 40px;
    width: 560px;
    height: 880px;
    overflow: hidden;
    box-shadow: 0 10px 30px rgba(0, 0, 0, 0.25);
  }
  .cover-backdrop {
    position: absolute;
    inset: 0;
    background:
      linear-gradient(to bottom,
        var(--sky-top) 0%,
        var(--sky-mid) 30%,
        var(--cloud-band) 46%,
        var(--horizon-gold) 58%,
        var(--horizon-ember) 64%,
        var(--sea-dusk) 72%,
        var(--foreground-dark) 88%,
        var(--foreground-dark) 100%);
  }
  .wine-glasses {
    position: absolute;
    left: 146px;
    top: 420px;
    width: 280px;
    height: 350px;
    border-radius: 46% 46% 20% 20% / 30% 30% 12% 12%;
    border: 2px solid rgba(138, 150, 184, 0.55);
    background:
      radial-gradient(ellipse 60% 30% at 50% 45%, var(--wine-gold), rgba(233, 193, 94, 0) 75%),
      linear-gradient(to bottom,
        rgba(185, 138, 58, 0.35) 0%,
        var(--wine-amber) 40%,
        rgba(60, 50, 40, 0.7) 75%,
        rgba(13, 15, 22, 0.9) 100%);
  }
  .cover-title {
    position: absolute;
    top: 22px;
    right: 52px;
    margin: 0;
    text-align: right;
    font-family: "Great Vibes", cursive;
    font-weight: 400;
    font-size: 80px;
    line-height: 1.1;
    color: var(--title-ink);
  }
  .cover-title .title-line {
    display: block;
  }
  .cover-author {
    position: absolute;
    left: 0;
    right: 0;
    bottom: 22px;
    margin: 0;
    text-align: center;
    font-family: "Great Vibes", cursive;
    font-weight: 400;
    font-size: 38px;
    letter-spacing: 1px;
    color: var(--author-ink);
  }
</style>
</head>
<body>
  <main class="canvas">
    <section class="book-cover">
      <div class="cover-backdrop" role="img" aria-label="Sunset over the sea under a deep blue cloudy sky"></div>
      <div class="wine-glasses" role="img" aria-label="Photograph of two glasses of white wine clinking in silhouetted hands in front of the sunset"></div>
      <h1 class="cover-title">
        <span class="title-line">Where Rivers</span>
        <span class="title-line">Bend</span>
      </h1>
      <p class="cover-author">Author name</p>
    </section>
  </main>
</body>
</html>
```